Brindle Recycling needs a new web design

We need a new web design for our company based in Austin, TX. We resell and recycling electronics such as laptops, computer components, Zelvotabs, Quorns, etc. Since our inception over ten years ago, we’ve become one of the premier electronics recycling and remarketing companies in Austin, Texas.

```html
<!DOCTYPE html>
<html lang="en">
<head>
<meta charset="utf-8">
<title>Brindle Recycling – Computer Recycling Made Easy</title>
<link href="https://fonts.googleapis.com/css2?family=Montserrat:wght@400;600;700&family=Open+Sans:wght@400;600;700&family=Tinos:wght@400;700&display=swap" rel="stylesheet">
<style>
:root{
  --blue:#1b75bc;
  --blue-dark:#0f5a97;
  --blue-light:#3d8fd1;
  --ink:#1e1e1e;
  --text:#555;
  --muted:#888;
  --line:#d9d9d9;
  --paper:#ffffff;
  --hero:#ececec;
  --footer:#2a2a2a;
  --footer-deep:#1f1f1f;
}
*{box-sizing:border-box;margin:0;padding:0}
html,body{width:1200px;height:3947px;overflow:hidden}
body{position:relative;background:var(--paper);font-family:"Open Sans",Arial,sans-serif;color:var(--text)}
.abs{position:absolute}
.serif{font-family:"Tinos","Times New Roman",serif}

/* top bar */
.topbar{left:0;top:0;width:1200px;height:37px;border-bottom:1px solid #eee;font-size:11px;color:#333;font-weight:600}
.topbar .item{top:11px;display:flex;align-items:center;gap:6px}
.follow{right:160px;top:11px;display:flex;align-items:center;gap:6px}
.dot{width:15px;height:15px;border-radius:50%;background:#9a9a9a}

/* nav */
.nav{left:0;top:37px;width:1200px;height:71px}
.brand{left:158px;top:10px;display:flex;align-items:center;gap:8px}
.brand .mark{width:46px;height:46px;border-radius:50%;border:3px solid var(--blue)}
.brand .name{font-family:"Montserrat",sans-serif;font-weight:700;font-size:18px;color:var(--blue);line-height:1.05;width:110px}
.menu{left:395px;top:0;height:71px;display:flex;font-family:"Montserrat",sans-serif;font-size:11px;font-weight:600;color:#333}
.menu a{display:flex;align-items:center;padding:0 15px;text-decoration:none;color:inherit}
.menu a.active{background:var(--blue);color:#fff}
.callbox{left:890px;top:0;width:150px;height:71px;background:var(--blue);color:#fff;font-family:"Montserrat",sans-serif;font-weight:700;font-size:13px;padding:17px 0 0 16px;line-height:1.4}

/* hero */
.hero{left:0;top:108px;width:1200px;height:467px;background:linear-gradient(180deg,#f4f4f4,#e3e3e3);border-bottom:4px solid #cfe1f1}
.hero-art{left:66px;top:22px;width:514px;height:410px;border-radius:6px;background:radial-gradient(circle at 45% 45%,#5aa0e0,#2d5d8f 55%,#cfd5db 80%,#e8e8e8)}
.hero h1{left:574px;top:100px;width:470px;font-size:52px;font-weight:400;color:#111;line-height:1.1;text-align:right}
.hero p{left:574px;top:236px;width:466px;text-align:right;font-size:14px;color:#444;line-height:1.6}
.pill{display:flex;align-items:center;gap:10px;background:#fff;border-radius:24px;box-shadow:0 2px 6px rgba(0,0,0,.15);font-family:"Montserrat",sans-serif;font-weight:700;font-size:11px;color:#222;padding:4px 4px 4px 18px}
.pill .arrow{width:30px;height:30px;border-radius:50%;background:var(--blue);display:flex;align-items:center;justify-content:center}
.hero .pill{left:908px;top:306px}
.slides{left:560px;top:417px;display:flex;gap:6px}
.slides span{width:18px;height:3px;background:#aaa}
.slides span:first-child{background:var(--blue)}

/* section headings */
.title{width:1200px;left:0;text-align:center;font-size:32px;color:#111;font-weight:400;letter-spacing:1px}
.tag{left:0;width:1200px;display:flex;justify-content:center}
.tag span{border-left:4px solid var(--blue);padding:2px 12px;font-family:"Montserrat",sans-serif;font-size:15px;color:#222;letter-spacing:.5px;border-bottom:1px solid var(--line)}

.about-copy{left:220px;top:742px;width:760px;text-align:center;font-size:13px;line-height:1.75;color:var(--muted)}

/* services */
.services{left:0;top:880px;width:1200px;height:436px;background:linear-gradient(120deg,#1768ad 0%,#2a82c8 45%,#1b6db1 100%)}
.services-texture{left:0;top:0;width:1200px;height:436px;background:radial-gradient(circle at 80% 30%,rgba(255,255,255,.18),transparent 45%),radial-gradient(circle at 20% 80%,rgba(0,0,0,.15),transparent 50%)}
.services .title{top:55px;color:#fff;font-size:30px}
.services .lead{left:158px;top:165px;width:380px;color:#fff;font-size:13px;line-height:1.6}
.card{background:#fff;top:141px;height:282px;padding:10px;text-align:center}
.card .visual{height:170px;display:flex;flex-direction:column;align-items:center;justify-content:center;color:#fff}
.card h3{margin-top:18px;font-family:"Montserrat",sans-serif;font-size:13px;font-weight:700;color:#111}
.card a{display:block;margin-top:4px;font-size:12px;color:#333;text-decoration:underline}
.eco{background:var(--blue)}
.eco strong{font-size:14px;text-decoration:underline;margin-bottom:8px}
.eco p{font-size:12px;width:150px;line-height:1.5}

/* capability */
.cap-title{top:1375px;font-size:32px}
.cap-ring{left:0;top:1316px}
.cap{width:290px;background:#fff}
.cap h4{background:var(--blue);color:#fff;text-align:center;font-family:"Montserrat",sans-serif;font-size:13px;font-weight:700;height:37px;line-height:37px;letter-spacing:1px}
.cap ul{list-style:none;padding:14px 0 0 26px;font-size:12px;color:#666;line-height:23px}
.cap li::before{content:"•";margin-right:6px;color:#999}

/* ceo */
.ceo-photo{left:163px;top:2240px;width:447px;height:352px;background:linear-gradient(135deg,#d9e3ea,#b7c7d3 55%,#8aa4b6)}
.ceo-callout{left:390px;top:2258px;width:220px;height:334px;background:var(--blue);color:#fff;padding:26px 20px;box-shadow:-4px 4px 0 rgba(0,0,0,.05)}
.ceo-callout p{font-family:"Montserrat",sans-serif;font-size:26px;font-weight:700;line-height:1.3}
.ceo-callout .more{position:absolute;left:20px;bottom:22px;font-family:"Montserrat",sans-serif;font-size:11px;font-weight:700}
.ceo h2{left:650px;top:2280px;font-size:30px;font-weight:400;color:#111;letter-spacing:1px}
.ceo h3{left:650px;top:2326px;font-family:"Montserrat",sans-serif;font-size:16px;font-weight:700;color:#111;border-bottom:2px solid var(--blue);padding-bottom:4px}
.ceo p.bio{left:650px;top:2374px;width:390px;font-size:12px;line-height:19px;color:#666}

/* certified banner */
.certified{left:0;top:2737px;width:1200px;height:245px;background:linear-gradient(90deg,#1a1a1a,#3b3b3b 50%,#222)}
.certified h2{top:60px;width:1200px;text-align:center;color:#fff;font-size:30px;font-weight:400;letter-spacing:.5px}
.certified h3{top:110px;width:1200px;text-align:center;color:#fff;font-family:"Montserrat",sans-serif;font-size:15px;font-weight:600}
.certified h3 span{text-decoration:underline}
.certified p{left:200px;top:150px;width:800px;text-align:center;color:#ddd;font-size:13px;line-height:1.6}

/* contact */
.contact-title{top:3040px}
.field{font-size:10px;color:#777;font-family:"Montserrat",sans-serif;letter-spacing:.5px}
.field .box{margin-top:6px;height:35px;border:1px solid var(--line)}
.contact .pill{left:535px;top:3377px}

/* footer */
.footer{left:0;top:3421px;width:1200px;height:343px;background:var(--footer)}
.foot-brand{left:158px;top:132px;width:150px;height:79px;background:#fff;display:flex;align-items:center;justify-content:center;gap:8px}
.foot-brand .mark{width:36px;height:36px;border-radius:50%;border:3px solid var(--blue)}
.foot-brand .name{font-family:"Montserrat",sans-serif;font-weight:700;font-size:14px;color:var(--blue);line-height:1.05;width:80px}
.foot-copy{left:368px;top:132px;width:672px;font-size:12.5px;line-height:1.55;color:#9a9a9a}
.info{top:262px;display:flex;gap:12px;align-items:flex-start;color:#bbb;font-size:12px;line-height:1.5}
.info b{font-weight:400;color:#999;font-size:11px}
.socials{left:888px;top:270px;display:flex;gap:10px}
.socials span{width:26px;height:26px;border-radius:50%;border:1px solid #777}
.quick{left:0;top:3764px;width:1200px;height:183px;background:var(--footer-deep)}
.quick h4{left:158px;top:20px;color:#fff;font-family:"Montserrat",sans-serif;font-size:13px;font-weight:700}
.qcol{top:56px;list-style:none;font-size:11.5px;color:#aaa;line-height:29px}
</style>
</head>
<body>

<!-- Top bar -->
<header class="abs topbar">
  <div class="abs item" style="left:158px">
    <svg width="14" height="10" viewBox="0 0 14 10"><rect x=".5" y=".5" width="13" height="9" fill="none" stroke="#1b75bc"/><path d="M.5 .5 7 6 13.5 .5" fill="none" stroke="#1b75bc"/></svg>
    dale@brindlerecycling.com
  </div>
  <div class="abs item" style="left:360px">
    <svg width="10" height="14" viewBox="0 0 10 14"><path d="M5 0C2 0 0 2.2 0 5c0 3.5 5 9 5 9s5-5.5 5-9C10 2.2 8 0 5 0z" fill="#1b75bc"/><circle cx="5" cy="5" r="1.8" fill="#fff"/></svg>
    4120 Pecan Ridge Rd Austin TX USA 78750
  </div>
  <div class="follow abs">Follow Us : <span class="dot"></span><span class="dot"></span><span class="dot"></span><span class="dot"></span></div>
</header>

<!-- Navigation -->
<nav class="abs nav">
  <div class="abs brand"><span class="mark"></span><span class="name">Brindle Recycling</span></div>
  <div class="abs menu">
    <a class="active" href="#">HOME</a><a href="#">ABOUT US</a><a href="#">SERVICES</a><a href="#">BOOK ONLINE</a><a href="#">CONTACT US</a>
  </div>
  <div class="abs callbox">CALL US :<br>(512) 555-0147</div>
</nav>

<!-- Hero -->
<section class="abs hero">
  <div class="abs hero-art" role="img" aria-label="Laptop, tablets and smartphones grouped together showing colourful app screens"></div>
  <h1 class="abs serif">Computer Recycling<br>Made Easy</h1>
  <p class="abs">We have a passion to keep our world clean and are here to guide you<br>through all the stages of the recycling process.</p>
  <div class="abs pill">CONTACT US <span class="arrow"><svg width="12" height="10" viewBox="0 0 12 10"><path d="M0 5h10M6 1l4 4-4 4" stroke="#fff" stroke-width="1.8" fill="none"/></svg></span></div>
  <div class="abs slides"><span></span><span></span><span></span></div>
</section>

<!-- About -->
<section class="about">
  <h2 class="abs title serif" style="top:638px">ABOUT US</h2>
  <div class="abs tag" style="top:690px"><span>Computer Recycling Made Easy</span></div>
  <p class="abs about-copy">What most people do not realize is electronic waste represents 2% of America's trash in landfills, but it equals 70% of overall toxic waste. Used computer equipment is a rapidly growing source of waste across the country. Only 12.5% of electronic waste is currently recycled in the US. Computers contain valuable parts that we can recycle, and heavy metals that we should try to keep out of landfills. Despite this, Texas has historically had low computer recycling rates in the past.</p>
</section>

<!-- Services -->
<section class="abs services">
  <div class="abs services-texture" role="img" aria-label="Blue-tinted close-up of a circuit board"></div>
  <h2 class="abs title serif">RECYCLING SERVICES</h2>
  <p class="abs lead">We have gained a large market share of the electronic waste recycling and electronics marketing business within Texas and throughout the country. Our customers have come to count on our hands on approach to every recycling job they send to us. We care about our customers and ensuring their recycling needs are met in the most environmentally sustainable ways. We are a true "Green Collar" company and our customers and employees appreciate this fact.</p>
  <div class="abs card" style="left:576px;width:240px">
    <div class="visual eco">
      <strong>Environmentally friendly</strong>
      <p>At Brindle Recycling, we strive to keep the environment serviced</p>
      <svg width="22" height="24" viewBox="0 0 22 24" style="margin-top:8px"><path d="M8 2v11l-3-3-2 2 6 8h9l2-9-8-2V2z" fill="#fff"/></svg>
    </div>
    <h3>ELECTRONIC RECYCLING</h3><a href="#">Schedule A pickup</a>
  </div>
  <div class="abs card" style="left:826px;width:214px">
    <div class="visual" role="img" aria-label="Worker sorting electronic scrap at a recycling facility" style="background:linear-gradient(135deg,#7a8a99,#c24b3c 55%,#5f6f7d)"></div>
    <h3>RECYCLING PICKUP</h3><a href="#">Schedule A pickup</a>
  </div>
</section>

<!-- Capability overview -->
<section class="capability">
  <h2 class="abs title serif cap-title">CAPABILITY OVERVIEW</h2>
  <svg class="abs cap-ring" width="1200" height="864" viewBox="0 0 1200 864" aria-hidden="true">
    <circle cx="600" cy="412" r="275" fill="none" stroke="#e3e3e3" stroke-width="2"/>
  </svg>
  <div class="abs cap" style="left:455px;top:1453px">
    <h4>RECYCLING</h4>
    <ul><li>Certified Global Recycling Capabilities</li><li>Sort by commodity</li><li>Certificate of Recycling</li><li>Data Destruction</li><li>Verifiable Certified Downstream Vendors</li></ul>
  </div>
  <div class="abs cap" style="left:171px;top:1692px">
    <h4>LOGISTICS</h4>
    <ul><li>Global Logistics Support</li><li>Global Warehouse Capabilities</li><li>Global Audit Capabilities</li><li>Inventory Management</li><li>Asset Management</li><li>Bill of Lading</li><li>Proof of Delivery</li><li>Transfer of Ownership (TOO)</li></ul>
  </div>
  <div class="abs cap" style="left:745px;top:1692px">
    <h4>CERTIFICATES</h4>
    <ul><li>R2:2013 Responsible Recycling Certified</li><li>ISO 14001:2015</li><li>OHSAS 18001:2007</li><li>State Commission on Environmental<br>&nbsp;&nbsp;&nbsp;Quality (SCEQ)</li><li>Registered Entity # RN00000000</li><li>GDPR Compliant</li><li>HIPAA Compliant</li></ul>
  </div>
  <div class="abs cap" style="left:455px;top:2000px">
    <h4>RETURN</h4>
    <ul><li>Market Value Pricing</li><li>Profit Sharing</li></ul>
  </div>
</section>

<div class="abs" style="left:0;top:2180px;width:1200px;height:1px;background:#eee"></div>

<!-- CEO -->
<section class="ceo">
  <div class="abs ceo-photo" role="img" aria-label="Portrait of two smiling team members in an office with recycling icons"></div>
  <div class="abs ceo-callout">
    <p>Dale is a calculated risk-taker with deep recycling industry</p>
    <span class="more">LEARN MORE →</span>
  </div>
  <h2 class="abs serif">DALE WHITCOMBE'S</h2>
  <h3 class="abs">CEO of Brindle Recycling</h3>
  <p class="abs bio">As the CEO of Brindle Recycling, Dale Whitcombe is responsible for running all facets of the business. Dale has a proven executive management track record and over 20 years of experience driving sales growth in the Recycling industry. Prior to founding Brindle Recycling in 2006, Dale was the Director of Sales for Lonestar Reclaim Trading Inc. and responsible for all global sales and marketing activities. At that firm he led the paradigm-shifting transformation into an enterprise-focused company while growing sales 50% year over year. Dale was able to accomplish these record-setting achievements because of his ability to build relationships, trust, and build rapport with everyone he meets. Today Brindle Recycling stands at the forefront of the Electronics Recycling industry by Dale's keen ability to see market solutions.</p>
</section>

<!-- Certified banner -->
<section class="abs certified" role="img" aria-label="Dark background photo of stacked electronic equipment">
  <h2 class="abs serif">WE ARE CERTIFIED FROM MERIDIAN REGISTRAR, INC</h2>
  <h3 class="abs"><span>The Environmental Management System is applicable</span></h3>
  <p class="abs">Processing of electronic assets and electronic scrap, all associated site operations and maintenance, as well as the supporting financial and administrative functions related to these activities and operations.</p>
</section>

<!-- Contact -->
<section class="contact">
  <h2 class="abs title serif contact-title">CONTACT US</h2>
  <div class="abs tag" style="top:3090px"><span>Computer Recycling Made Easy</span></div>
  <div class="abs field" style="left:263px;top:3150px;width:158px">NAME<div class="box"></div></div>
  <div class="abs field" style="left:437px;top:3150px;width:158px">EMAIL<div class="box"></div></div>
  <div class="abs field" style="left:608px;top:3150px;width:158px">SUBJECT<div class="box"></div></div>
  <div class="abs field" style="left:779px;top:3150px;width:158px">PHONE<div class="box"></div></div>
  <div class="abs field" style="left:263px;top:3214px;width:674px">MESSAGE<div class="box" style="height:113px"></div></div>
  <div class="abs pill">SUBMIT <span class="arrow"><svg width="12" height="10" viewBox="0 0 12 10"><path d="M0 5h10M6 1l4 4-4 4" stroke="#fff" stroke-width="1.8" fill="none"/></svg></span></div>
</section>

<!-- Footer -->
<footer class="abs footer">
  <div class="abs foot-brand"><span class="mark"></span><span class="name">Brindle Recycling</span></div>
  <p class="abs foot-copy">What most people do not realize is electronic waste represents 2% of America's trash in landfills, but it equals 70% of overall toxic waste. Used computer equipment is a rapidly growing source of waste across the country. Only 12.5% of electronic waste is currently recycled in the US. Computers contain valuable parts that we can recycle...</p>
  <div class="abs info" style="left:158px">
    <svg width="16" height="20" viewBox="0 0 10 14"><path d="M5 0C2 0 0 2.2 0 5c0 3.5 5 9 5 9s5-5.5 5-9C10 2.2 8 0 5 0z" fill="#bbb"/><circle cx="5" cy="5" r="1.8" fill="#2a2a2a"/></svg>
    <div><b>ADDRESS :</b><br>4120 Pecan Ridge Rd Austin TX</div>
  </div>
  <div class="abs info" style="left:418px">
    <svg width="18" height="18" viewBox="0 0 18 18"><path d="M4 1l3 4-2 2c1 2 3 4 5 5l2-2 4 3-2 3C8 16 2 10 1 3z" fill="#bbb"/></svg>
    <div><b>Call Us :</b><br>(512) 555-0147</div>
  </div>
  <div class="abs info" style="left:620px">
    <svg width="18" height="13" viewBox="0 0 14 10"><rect x=".5" y=".5" width="13" height="9" fill="none" stroke="#bbb"/><path d="M.5 .5 7 6 13.5 .5" fill="none" stroke="#bbb"/></svg>
    <div><b>EMAIL :</b><br>dale@brindlerecycling.com</div>
  </div>
  <div class="abs socials"><span></span><span></span><span></span><span></span></div>
</footer>

<section class="abs quick">
  <h4 class="abs">QUICK LINKS</h4>
  <ul class="abs qcol" style="left:158px"><li>Home</li><li>About US</li><li>Services</li><li>Contact Us</li></ul>
  <ul class="abs qcol" style="left:337px"><li>Book Online</li><li>Help</li><li>Support</li><li>Account</li></ul>
  <ul class="abs qcol" style="left:516px"><li>SiteMap</li><li>Sign Up</li><li>Register</li><li>Contact</li></ul>
  <ul class="abs qcol" style="left:674px"><li>Capabilities Overview</li><li>Company Info</li><li>Login</li></ul>
  <ul class="abs qcol" style="left:862px;line-height:22px;top:52px"><li>Copyright 2018 © brindlerecycling.<br>All Rights Reserved.</li><li>Privacy Policy</li><li>Terms and Condition</li></ul>
</section>

</body>
</html>
```